Church Website with Home Page and Member Sermon Library

I am in need of an updated design for our church website. This will include 4 pages (outlined below). We are a conservative, evangelical, Christian church. The site should be modern and clean, while still reflecting our conservative values. I already have a logo for our church, and I want the site to incorporate the logo, and match the logo/branding. Stock photos are allowed if needed, but I have uploaded some images of our church and would prefer those images to be used if possible. Any stock photos used should not include any people in the photos (scenery, nature, buildings, animals, etc. are fine).

The site will need 4 pages: Home, Support Us (Donate), Login, and Recording Library.

Page 1: Home
The home page should include the following sections:

- Navigation: Should include links to each section of the home page plus a "listen live" link which will take the user to a live-streaming site and a "support us" link which will take the user to a support/donate page.

- Announcements: Can be either a banner or some other design, but there needs to be some way for us to post announcements for visitors to see. I'm open for creative ideas in this section, but would like it not to take up a lot of room on the page.

- About Us: Should include address, service times (see attached document), and information about the church.

- Pastor Bio: A section that introduces our pastor and gives a short bio about our pastor. Would like this section to include a picture of our pastor. Somewhere in this section I would like to include this Bible reference: "And I will give you pastors according to mine heart, which shall feed you with knowledge and understanding. Jer 3:15 LPW"

- Articles of Faith (What We Believe): This should include several sub-sections each with a heading, body, and possibly 1 or more scripture references. I have attached a document to the brief that includes our articles of faith. Feel free to be creative with this section in how you lay these out and format them.

- Support Us: A small section that explains what kind of support someone can give and a link to a donation page. The link can say something like "Support Us" or "Donate Now".

- Contact form: A contact form that allows the visitor to send us a message. The contact form should ask for name, email, phone, and message.

- Footer: A footer that will be displayed on all pages of the site. This should include at a minimum a link to the home page (or a link to each individual section in the home page if you prefer), a link to "listen live", a link to "support us", a link to "contact us" (or you can put the contact form directly in the footer if you prefer), the address, and a "member login" link.

Page 2: Support Us
The donation page should include a form the visitor can fill out to make a donation. We will embed a third party form later. For this design, please just mock out the design with a basic form asking for name, phone, and email.

Page 3: Login
The recording library (detailed below) will require members to login with a shared numeric code before accessing the page. We need a design for a login screen. The screen should include navigation/footer just like all other pages, but the body of the login page will consist only of a form that asks the user to enter the access code and then a "login" button.

Page 4: Recording Library

The library page is a member-only page that will require a shared, numeric pass code to access. On this page, members will be able to access a filterable list of past sermons. The page by default should display most recent sermons, but should also include a search form that allows the member to filter the sermon list to find a particular sermon. The search form should allow the user to select a filter type (e.g. Speaker name, date, event, etc.) and type in a value to search. They should be able to add multiple filters and remove filters that have been added. Each sermon that is displayed in the result list should include basic information such as title, date, speaker, tags, etc. along with a download icon, and an embedded audio player where they can click a play button to stream it on-demand. Each sermon should also have clickable tags associated with it that can be used to find related sermons.
Updates

I have uploaded several images of our church. Feel free to incorporate these into your design if possible.

Target Market(s)

Church Members

Industry/Entity Type

Religion

Number of Pages Required

4 page

Font styles to use
Sans Serif

Colors

Designer to choose colors to be used in the design.

Requirements
Must have
• Must incorporate the logo (attached)
Nice to have
• Would like the design to incorporate pictures of our church (attached) instead of stock photos if possible.
Should not have
• Please avoid an overly cluttered design. Stock photos used should not include any people in the photos.

```html
<!DOCTYPE html>
<html lang="en">
<head>
<meta charset="utf-8">
<title>Member Sign In – Grace Hollow Chapel</title>
<link rel="stylesheet" href="https://fonts.googleapis.com/css2?family=Cinzel:wght@400;600&family=Montserrat:wght@400;500&display=swap">
<style>
  :root {
    --green: #86a96f;
    --ink: #111111;
    --text: #333333;
    --muted: #666666;
    --line: #d9d9d9;
    --footer-bg: #2b2b2b;
    --footer-text: #c9c9c9;
    --footer-rule: #3a3a3a;
    --pill-bg: #f4f1ef;
    --white: #ffffff;
  }
  * { box-sizing: border-box; margin: 0; padding: 0; }
  html, body { width: 1200px; height: 1018px; overflow: hidden; background: var(--white); }
  body { position: relative; font-family: 'Montserrat', sans-serif; color: var(--text); }

  .site-header { position: absolute; top: 0; left: 0; width: 1200px; height: 140px; }
  .brand {
    position: absolute; left: 173px; top: 40px; width: 150px;
    font-family: 'Cinzel', serif; font-weight: 400; font-size: 22px; line-height: 1.15;
    color: var(--green); text-align: center; letter-spacing: 1px;
  }
  .main-nav { position: absolute; top: 33px; left: 632px; display: flex; gap: 56px; }
  .main-nav a { color: var(--text); text-decoration: none; font-size: 15.5px; font-weight: 500; }

  .signin-card {
    position: absolute; left: 388px; top: 210px; width: 425px; height: 332px;
    border: 1px solid var(--line); background: var(--white);
  }
  .signin-title {
    position: absolute; top: 30px; width: 100%; text-align: center;
    font-family: 'Cinzel', serif; font-weight: 400; font-size: 37px; letter-spacing: 4px; color: var(--ink);
  }
  .title-rule { position: absolute; left: 130px; top: 94px; width: 163px; height: 3px; background: var(--ink); }
  .title-rule-thin { position: absolute; left: 172px; top: 100px; width: 79px; height: 1px; background: var(--ink); }
  .field-label { position: absolute; left: 37px; top: 127px; font-size: 14px; letter-spacing: 1px; color: var(--muted); }
  .field-input {
    position: absolute; left: 37px; top: 150px; width: 349px; height: 44px;
    border: 1px solid var(--line); border-radius: 3px; background: var(--white);
  }
  .remember { position: absolute; left: 38px; top: 213px; display: flex; align-items: center; gap: 6px; font-size: 14px; letter-spacing: 1px; color: var(--muted); }
  .remember-box { width: 13px; height: 13px; border: 1px solid var(--line); border-radius: 2px; background: #f7f7f7; }
  .login-button {
    position: absolute; left: 36px; top: 249px; width: 352px; height: 40px; border: none;
    background: var(--green); color: var(--white);
    font-family: 'Cinzel', serif; font-weight: 600; font-size: 15px; letter-spacing: 0.5px;
  }

  .site-footer { position: absolute; left: 0; top: 629px; width: 1200px; height: 389px; background: var(--footer-bg); color: var(--footer-text); }
  .listen-live {
    position: absolute; left: 178px; top: 118px; width: 222px; height: 64px;
    border: 2px solid var(--green); border-radius: 32px; background: var(--pill-bg);
    box-shadow: 0 8px 18px rgba(0,0,0,0.35);
  }
  .listen-live-icon { position: absolute; left: 3px; top: 3px; width: 56px; height: 56px; border-radius: 50%; background: var(--green); }
  .listen-live-label { position: absolute; left: 79px; top: 21px; font-family: 'Cinzel', serif; font-weight: 600; font-size: 15px; color: var(--green); }
  .footer-heading { position: absolute; font-family: 'Cinzel', serif; font-weight: 400; font-size: 16px; letter-spacing: 1.2px; color: var(--white); }
  .location-heading { left: 186px; top: 215px; }
  .address { position: absolute; left: 186px; top: 244px; display: flex; gap: 8px; font-size: 13.5px; line-height: 17px; color: var(--footer-text); }
  .footer-brand {
    position: absolute; left: 480px; top: 190px; width: 240px; text-align: center;
    font-family: 'Cinzel', serif; font-weight: 400; font-size: 30px; line-height: 1.15; color: var(--green);
  }
  .quick-heading { left: 826px; top: 107px; }
  .quick-links { position: absolute; left: 826px; top: 145px; list-style: none; }
  .quick-links li { height: 27.5px; font-size: 13.5px; }
  .quick-links a { color: var(--footer-text); text-decoration: none; }
  .footer-rule { position: absolute; left: 0; top: 317px; width: 1200px; height: 1px; background: var(--footer-rule); }
  .copyright { position: absolute; left: 178px; top: 340px; font-size: 12px; color: var(--footer-text); }
  .social { position: absolute; left: 913px; top: 341px; display: flex; gap: 16px; }
  .social a { display: block; width: 11px; height: 11px; border-radius: 50%; background: var(--white); }
</style>
</head>
<body>
  <header class="site-header">
    <div class="brand">Grace Hollow Chapel</div>
    <nav class="main-nav">
      <a href="#">About Us</a>
      <a href="#">Articles Of Faith</a>
      <a href="#">Contact Us</a>
    </nav>
  </header>

  <main>
    <form class="signin-card">
      <h1 class="signin-title">SIGN IN</h1>
      <div class="title-rule"></div>
      <div class="title-rule-thin"></div>
      <label class="field-label">Password</label>
      <div class="field-input"></div>
      <div class="remember"><span class="remember-box"></span>Remember me</div>
      <button class="login-button" type="button">LOGIN</button>
    </form>
  </main>

  <footer class="site-footer">
    <a class="listen-live" href="#">
      <span class="listen-live-icon">
        <svg width="56" height="56" viewBox="0 0 56 56" fill="none" stroke="#fff" stroke-width="2" stroke-linecap="round">
          <circle cx="28" cy="24" r="2.5" fill="#fff"/>
          <path d="M22 18a8 8 0 0 0 0 12M34 18a8 8 0 0 1 0 12M18 14a14 14 0 0 0 0 20M38 14a14 14 0 0 1 0 20"/>
          <rect x="20" y="36" width="16" height="8" rx="1.5" fill="#fff" stroke="none"/>
        </svg>
      </span>
      <span class="listen-live-label">LISTEN LIVE</span>
    </a>

    <h2 class="footer-heading location-heading">LOCATION</h2>
    <div class="address">
      <svg width="11" height="14" viewBox="0 0 11 14" fill="none" stroke="#86a96f" stroke-width="1.3"><path d="M5.5 13s4.5-4.6 4.5-7.7A4.5 4.5 0 0 0 1 5.3C1 8.4 5.5 13 5.5 13z"/><circle cx="5.5" cy="5.3" r="1.6"/></svg>
      <span>418 Cedar Ridge Ln. Fairview,<br>Ohio 43210</span>
    </div>

    <div class="footer-brand">Grace Hollow Chapel</div>

    <h2 class="footer-heading quick-heading">QUICK LINKS</h2>
    <ul class="quick-links">
      <li><a href="#">About Us</a></li>
      <li><a href="#">Articles Of Faith</a></li>
      <li><a href="#">Support Our Ministry</a></li>
      <li><a href="#">Contact Us</a></li>
      <li><a href="#">Member Login</a></li>
    </ul>

    <div class="footer-rule"></div>
    <p class="copyright">Copyright 2023 Grace Hollow Chapel I All rights reserved</p>
    <nav class="social">
      <a href="#" aria-label="Social profile one"></a>
      <a href="#" aria-label="Social profile two"></a>
      <a href="#" aria-label="Social profile three"></a>
      <a href="#" aria-label="Video channel"></a>
    </nav>
  </footer>
</body>
</html>
```